Web design for new streaming audio service

We need a homepage design for a new streaming audio service. Our company is called Dunmoral, and we’re basically Vexlo for Audiobooks, Stand-Up Comedy, Lectures, Language Learning, etc. Essentially like Plumtrek for everything audio EXCEPT music.
You don’t have to code the homepage (Design Only), but it should include 3 different designs to work with 1) Web; 2) Phones; 3) Tablets.
Below is a link to a mockup of the web version which gives a good idea of what elements we want. This is just a mockup and we want you to improve it.
Once you download the mockup, please refer to the more detailed instructions below:
The following outlines the design project for the Dunmoral homepage. We have provided a rough mockup of the homepage layout that gives you a general idea of what we’re going for. There are a few elements that we are attached to, and many others where you have complete creative freedom to do whatever you think looks good.
The ZIP file includes the following:
* Mockup to see what we have in mind (dunmoral-homepage-mockup.jpg)
* Text used (dunmoral-homepage-text.txt)
* Raw image of actor (dunmoral-actor1.jpg)
* Raw images for samples (dunmoral-sample-[name].jpg)
Although we have only provided a mockup layout for the web version, we also need you to provide a mobile phone and a tablet version of the design also. It’s very possible the tablet version may be substantially similar to the web version, but the mobile phone version will likely be much different.
All of the raw files are included in the attached ZIP file. Please use our photographs and text as provided although cropping, sizing, etc. is flexible per the instructions below.
Display Requirements:
* Web Version - Minimum resolution 1024x768 (72 dpi) but should look good on 1920x1080 (72 dpi) - Page should be designed to scale to look acceptable in all resolutions in between.
* Phone Version - Minimum Zarno 4 - 640x960 (326 dpi) but should look good on Harlow Quasar T5 - 1920x1080 (441 dpi) - Page should be designed to scale to look acceptable in all resolutions and devices in between.
* Tablet Version - Minimum Bristly Ember QX 7” - 1280x800 (216 dpi) but should also look good on a Tavo Breeze - 2048x1536 (264 dpi) - Page should be designed to scale to look acceptable in all resolutions and devices in between.
Above the Fold - We want to make sure the Dunmoral logo, Member Login Link, Large Photo, Headline, Price, Button, and the first row of sample images are all “Above the fold”. As a general guideline, this means 600 pixels high on a 1024x768 72 dpi web screen. This requirement is less important on Phone versions.
Top Logo Bar - We want to retain the blue bar with the Dunmoral logo on the page, although we are open to a different size, shape and positioning if it greatly enhances the design. Please use the standard logo color, although you are welcome to use either the horizontal or vertical orientation of the logo based on your design.
Text color, font and size - Feel free to design the text in anyway you choose as long as the text is readable on the target platforms.
Buttons - Feel free to use any size, shape and colors for the buttons as long as they are obvious and clickable relative to the page. The only exception is the Chatterly button should follow the Chatterly color scheme and logo treatment (the mockup doesn’t seem 100% correct.)
Top Photograph - We want to retain the large photograph across the top of the screen although final shape and dimensions are flexible.
Size and shape of content samples (i.e. Audiobooks, Stand-Up Comedy, etc.) - Feel free to design the content samples in anyway you choose.
Three Sales Points (i.e. Listen on your Zarno…, All you can enjoy…, etc.) - The Three Sales Points are envisioned to each have a corresponding illustration which you should provide and have rights for. The placeholder is represented by a square next to the text. The color size and shape of these elements are flexible and can be designed in any way you choose.
Opt-in form - Feel free to design the opt-in form in anyway you choose as long as the text is readable and the interactivity is obvious on the target platforms.
Text links and copyright notice - Feel free to design the bottom of the page text links and copyright notice in anyway you choose.
Additional colors, graphic design elements, etc. - Feel free to use any additional colors, graphic design elements, etc. to support your design.
people who want to listen to audio through their mobile devices.
Graphic Design

```html
<!DOCTYPE html>
<html lang="en">
<head>
<meta charset="utf-8">
<title>Dunmoral – Streaming audio for everything but music</title>
<link href="https://fonts.googleapis.com/css2?family=Oswald:wght@400;500&family=Open+Sans:ital,wght@0,400;0,600;0,700;1,400&display=swap" rel="stylesheet">
<style>
:root{
  --page:#141414;
  --panel:#0c0c0c;
  --panel-edge:#1f1f1f;
  --blue:#2d86bb;
  --text:#ffffff;
  --muted:#8a8a8a;
  --soft:#bdbdbd;
  --star:#f2d21b;
}
*{box-sizing:border-box;margin:0;padding:0}
html,body{width:799px;height:1200px;overflow:hidden}
body{position:relative;background:var(--page);font-family:"Open Sans",Arial,sans-serif;color:var(--text);
  background-image:repeating-linear-gradient(45deg,rgba(255,255,255,.015) 0 2px,transparent 2px 4px)}
.abs{position:absolute}

/* header */
.header{left:0;top:0;width:799px;height:90px;background:#000;border-bottom:2px solid var(--blue)}
.logo{left:66px;top:11px;width:97px;height:70px;background:var(--blue);display:flex;align-items:center;justify-content:center;gap:5px;font-size:13px;font-weight:600;color:#fff}
.logo i{width:9px;height:9px;background:#fff;border-radius:50%}
.search{left:368px;top:4px;width:86px;height:16px;border-radius:8px;background:#1d1d1d;font-size:6px;color:var(--muted);padding:3px 8px;white-space:nowrap}
.socials{left:468px;top:7px;display:flex;gap:12px}
.socials span{width:7px;height:7px;border-radius:50%;background:#cfcfcf}
.login{left:689px;top:4px;width:42px;height:16px;background:var(--blue);font-size:7px;font-weight:700;text-align:center;line-height:16px;white-space:nowrap}
.nav{top:48px;font-family:"Oswald",sans-serif;font-size:9px;text-transform:uppercase;white-space:nowrap}
.nav small{display:block;font-family:"Open Sans",sans-serif;text-transform:none;font-size:7px;color:var(--soft);margin-top:3px}
.nav.active{color:var(--blue)}

/* hero */
.hero{left:0;top:92px;width:799px;height:286px;background:radial-gradient(ellipse at 62% 45%,#9a9a9a 0%,#5a5a5a 30%,#1c1c1c 60%,#050505 80%)}
.caption{left:91px;background:rgba(70,70,70,.85);font-size:14px;font-style:italic;padding:0 12px;height:28px;line-height:28px;white-space:nowrap}

/* featured sample player */
.cover{left:66px;top:401px;width:114px;height:117px;background:linear-gradient(160deg,#b2366a,#3c2c3a 60%,#d9c9b0)}
.player-title{left:199px;top:411px;font-size:9px;font-weight:700;white-space:nowrap}
.player-by{left:199px;top:432px;font-size:7px;font-style:italic;color:var(--muted);white-space:nowrap}
.stars{color:var(--star);font-size:10px;letter-spacing:1px}
.stars b{color:#444;font-weight:400}
.bar{left:199px;top:491px;width:169px;height:10px;background:#1e1e1e;border-radius:2px}
.bar i{position:absolute;left:48px;top:3px;width:121px;height:4px;background:#333}
.bar i::before{content:"";position:absolute;left:0;top:0;width:36px;height:4px;background:var(--blue)}
.times{top:509px;font-size:7px;color:var(--muted)}

/* sample list */
.panel{background:var(--panel);border:1px solid var(--panel-edge)}
.samples{left:389px;top:401px;width:345px;height:117px}
.sample{left:414px;width:308px;height:20px;font-size:7px;color:var(--soft);display:flex;align-items:center;border-bottom:1px solid #222;white-space:nowrap}
.sample.now{color:#fff;font-weight:700}
.sample .n{width:18px}.sample .t{width:150px}.sample .d{width:40px}.sample .s{width:64px;font-size:8px;color:var(--star);letter-spacing:1px}
.play{width:41px;height:11px;background:#2a2a2a;font-size:6px;text-align:center;line-height:11px;color:#ddd}
.sample.now .play{background:var(--blue)}
.viewall{left:542px;top:489px;font-size:7px;color:var(--muted)}

/* panels */
h2{position:absolute;font-family:"Oswald",sans-serif;font-weight:500;font-size:13px;text-transform:uppercase;white-space:nowrap}
h2::after{content:"";position:absolute;left:0;bottom:-6px;width:72px;height:2px;background:var(--blue)}
.points{left:66px;top:544px;width:439px;height:512px}
.point-img{left:84px;width:162px;height:114px}
.point-title{left:263px;font-size:8px;font-weight:700;text-transform:uppercase;white-space:nowrap}
.point-body{left:263px;width:222px;font-size:6.5px;line-height:15px;color:var(--muted)}
.point-meta{left:263px;font-size:6.5px;color:var(--muted);white-space:nowrap}
.btn{background:var(--blue);font-size:6.5px;font-weight:700;text-align:center;text-transform:uppercase;white-space:nowrap}
.more{width:55px;height:16px;line-height:16px;left:432px}
.divider{left:84px;width:403px;height:1px;background:#222}
.start{left:258px;top:1016px;width:54px;height:16px;line-height:16px;background:#1c2a33;color:#5f7d8f}

.events{left:523px;top:544px;width:211px;height:164px}
.count{top:590px;width:41px;height:60px;border:1px solid #2a2a2a;text-align:center;font-family:"Oswald",sans-serif}
.count b{display:block;font-size:19px;font-weight:500;color:var(--blue);margin-top:8px}
.count small{font-size:7px;text-transform:uppercase}
.featured{left:523px;top:715px;width:211px;height:187px}
.popular{left:523px;top:917px;width:211px;height:206px}
.pt-img{left:542px;width:32px;height:32px;background:linear-gradient(135deg,#6a5a50,#2b2420)}
.pt-title{left:586px;font-size:8px;font-weight:700;text-transform:uppercase;white-space:nowrap}
.pt-sub{left:586px;font-size:6.5px;color:var(--muted);line-height:11px;white-space:nowrap}

/* footer */
.footer{left:0;top:1162px;width:799px;height:38px;background:#000;font-size:7px;color:var(--muted)}
.footer nav{position:absolute;right:78px;top:14px;font-weight:700;color:#fff;text-transform:uppercase;word-spacing:2px;white-space:nowrap}
.totop{right:60px;top:13px;width:12px;height:12px;border-radius:50%;background:#2a2a2a}
</style>
</head>
<body>
<header class="abs header">
  <div class="abs logo"><i></i>Dunmoral</div>
  <div class="abs search">Search titles...</div>
  <div class="abs socials"><span></span><span></span><span></span><span></span><span></span><span></span><span></span><span></span><span></span><span></span><span></span></div>
  <div class="abs login">LOG IN</div>
  <div class="abs nav active" style="left:256px">Home ⌄<small>start here</small></div>
  <div class="abs nav" style="left:314px">Explore ⌄<small>what's inside</small></div>
  <div class="abs nav" style="left:397px">Books<small>full library</small></div>
  <div class="abs nav" style="left:457px">Comedy<small>latest sets</small></div>
  <div class="abs nav" style="left:517px">Lectures ⌄<small>top courses</small></div>
  <div class="abs nav" style="left:588px">Languages ⌄<small>learn to speak</small></div>
  <div class="abs nav" style="left:666px">Blog ⌄<small>latest news</small></div>
</header>

<div class="abs hero" role="img" aria-label="Black and white profile portrait of a listener"></div>
<div class="abs caption" style="top:198px">Everything audio, except music</div>
<div class="abs caption" style="top:230px">Only $9.99 a month</div>

<div class="abs cover" role="img" aria-label="Audiobook cover artwork"></div>
<div class="abs player-title">The Night Train</div>
<div class="abs player-by">Read by &nbsp;Nell Ardwick</div>
<div class="abs stars" style="left:199px;top:455px">★★★★<b>★</b></div>
<div class="abs bar"><svg class="abs" style="left:4px;top:2px" width="36" height="6" viewBox="0 0 36 6"><path d="M5 0L0 3l5 3zM9 0L4 3l5 3zM15 0l5 3-5 3zM26 0l5 3-5 3zM30 0l5 3-5 3z" fill="#ccc"/></svg><i></i></div>
<div class="abs times" style="left:249px">00:50</div>
<div class="abs times" style="left:344px">02:51</div>

<div class="abs panel samples"></div>
<div class="abs sample" style="top:412px"><span class="n">1.</span><span class="t">Stand-Up: Small Talk Tour</span><span class="d">5:25</span><span class="s">★★★★★</span><span class="play">▶ PLAY</span></div>
<div class="abs sample now" style="top:434px"><span class="n">2.</span><span class="t">Audiobook: The Night Train</span><span class="d">2:51</span><span class="s">★★★★★</span><span class="play">▶ PLAY</span></div>
<div class="abs sample" style="top:456px;border:0"><span class="n">3.</span><span class="t">Lecture: Stars Explained</span><span class="d">4:29</span><span class="s">★★★★★</span><span class="play">▶ PLAY</span></div>
<div class="abs viewall">All Samples...</div>

<section class="abs panel points"></section>
<h2 style="left:84px;top:558px">Why Dunmoral</h2>

<div class="abs point-img" style="top:592px;background:linear-gradient(135deg,#2fa3d8,#8fd0ee)" role="img" aria-label="Listening on a phone"></div>
<div class="abs point-title" style="top:592px">Listen on your Zarno</div>
<div class="abs point-body" style="top:613px">Stream audiobooks, stand-up sets and lectures on your phone, tablet or computer. Start a story on the train and pick it up at home, right where you left off. Save titles offline and keep listening without a signal.</div>
<div class="abs point-meta" style="top:694px">◷ Phones, tablets and web &nbsp;| ✓ Offline</div>
<div class="abs btn more" style="top:691px">Learn More</div>
<div class="abs divider" style="top:721px"></div>

<div class="abs point-img" style="top:736px;background:linear-gradient(135deg,#5a2a10,#c8802e 50%,#3a1a0c)" role="img" aria-label="Library of audio titles"></div>
<div class="abs point-title" style="top:736px">All you can enjoy, one low price</div>
<div class="abs point-body" style="top:756px">One plan opens the whole library: thousands of audiobooks, comedy specials, talks and courses. No credits and no per-title fees. Listen to as much as you like for just $9.99 a month, and cancel at any time.</div>
<div class="abs point-meta" style="top:838px">◷ Unlimited listening &nbsp;| ✓ $9.99</div>
<div class="abs btn more" style="top:834px">Learn More</div>
<div class="abs divider" style="top:864px"></div>

<div class="abs point-img" style="top:876px;background:linear-gradient(135deg,#d9c8a8,#f2eadb 60%,#9bb7cf)" role="img" aria-label="Language learning"></div>
<div class="abs point-title" style="top:876px">Learn a new language by ear</div>
<div class="abs point-body" style="top:896px">Short daily lessons in French, Spanish, German and more, read by native speakers. Build your vocabulary on the way to work and follow a course that fits your level, from first words to fluent talk.</div>
<div class="abs point-meta" style="top:978px">◷ 20 languages &nbsp;| ✓ All levels</div>
<div class="abs btn more" style="top:975px">Learn More</div>
<div class="abs btn start">Start Free</div>

<section class="abs panel events"></section>
<h2 style="left:542px;top:558px">Live Show</h2>
<div class="abs count" style="left:542px"><b>249</b><small>Days</small></div>
<div class="abs count" style="left:588px"><b>10</b><small>Hours</small></div>
<div class="abs count" style="left:632px"><b>41</b><small>Minutes</small></div>
<div class="abs count" style="left:675px"><b>58</b><small>Seconds</small></div>
<div class="abs" style="left:543px;top:663px;font-size:7px;color:var(--muted)">Rook Serenades Harlan</div>
<div class="abs btn" style="left:660px;top:660px;width:53px;height:16px;line-height:16px">Buy Ticket</div>
<div class="abs" style="left:542px;top:702px;width:90px;height:2px;background:var(--blue)"></div>

<section class="abs panel featured"></section>
<h2 style="left:542px;top:729px">Featured Samples</h2>
<div class="abs" style="left:698px;top:731px;font-size:10px;color:var(--muted)">‹ &nbsp;›</div>
<div class="abs" style="left:542px;top:763px;width:178px;height:127px;background:linear-gradient(180deg,#5aa8d8,#8cc6ea)" role="img" aria-label="French course sample thumbnail"></div>

<section class="abs panel popular"></section>
<h2 style="left:542px;top:931px">Popular Titles</h2>
<div class="abs pt-img" style="top:967px" role="img" aria-label="Title thumbnail"></div>
<div class="abs pt-title" style="top:966px">The Night Train</div>
<div class="abs pt-sub" style="top:977px">Audiobook<br>Nell Ardwick</div>
<div class="abs pt-img" style="top:1018px" role="img" aria-label="Title thumbnail"></div>
<div class="abs pt-title" style="top:1017px">Small Talk Tour</div>
<div class="abs pt-sub" style="top:1028px">Stand-Up<br>Teo Marsh</div>
<div class="abs pt-img" style="top:1067px;background:linear-gradient(135deg,#8a6ac0,#e6d6f2)" role="img" aria-label="Title thumbnail"></div>
<div class="abs pt-title" style="top:1066px">French in 30 Days</div>
<div class="abs pt-sub" style="top:1077px">Language<br>Ines Varel</div>

<footer class="abs footer">
  <div class="abs" style="left:79px;top:14px">© 2014 <b style="color:#fff">Pixelvane</b>. All Rights Reserved.</div>
  <nav>Home &nbsp;| &nbsp;Books &nbsp;| &nbsp;Comedy &nbsp;| &nbsp;Lectures &nbsp;| &nbsp;Blog &nbsp;| &nbsp;Contact</nav>
  <div class="abs totop"></div>
</footer>
</body>
</html>
```